Design and Renovation Company Luxury Business Card

I want to create a luxury business card for a Design and Renovation Firm . We will use our current logo. The company name is 528BUILDA. We do not want anything standard. We need a very unique concept.
Please see uploaded inspiration. I really like the textured paper option. I would like the card to be thick with debossing, and/or embossing options. The logo has orange in it but I would like to see the card with and without the orange. I think the orange may make the company feel less high-end. The goal is to elevate the logo not match its vibe per se of the logo. We want something very unique, not standard at all!
I would like a space for :
Logo,
Name,
Position,
Email,
Office number,
Website Address,
Business Address,
Thank you!
Have fun!
Target Market(s)
Home owners Age 35 +
Industry/Entity Type
Design and Renovation
Contact Information for Business Card
Logo, Name, Position, Email, Office number, Website Address, Business Address,.
Colors
Designer to choose colors to be used in the design.
Requirements
Must have
- A luxury designer feel. Must be black or dark grey but open to other luxury ideas.
Nice to have
- Gold, silver, black embossing or debossing. Textured paper design.
Should not have
- A cheap look and feel.

```html
<!DOCTYPE html>
<html lang="en">
<head>
<meta charset="utf-8">
<title>528BUILDA Business Card</title>
<link rel="stylesheet" href="https://fonts.googleapis.com/css2?family=Roboto:wght@400;500;700&display=swap">
<style>
  :root {
    --backdrop-light: #d6d6d6;
    --backdrop-dark: #9c9c9c;
    --card-black: #0e0e0e;
    --card-black-soft: #1a1a1a;
    --accent-orange: #f7951f;
    --text-white: #ffffff;
  }
  * { margin: 0; padding: 0; box-sizing: border-box; }
  html, body {
    width: 1200px;
    height: 800px;
    overflow: hidden;
  }
  body {
    background: linear-gradient(135deg, var(--backdrop-dark) 0%, var(--backdrop-light) 100%);
    font-family: "Roboto", Arial, sans-serif;
    position: relative;
  }
  .business-card {
    position: absolute;
    top: 245px;
    width: 540px;
    height: 310px;
    border-radius: 18px;
    background: radial-gradient(ellipse at 40% 35%, var(--card-black-soft) 0%, var(--card-black) 70%);
    box-shadow: 0 3px 0 var(--accent-orange), 0 14px 30px rgba(0, 0, 0, 0.35);
    overflow: hidden;
    color: var(--text-white);
  }
  .card-front { left: 40px; }
  .card-back { left: 620px; }

  .identity {
    position: absolute;
    left: 68px;
    top: 42px;
  }
  .person-name {
    font-size: 22px;
    font-weight: 700;
    color: var(--accent-orange);
    letter-spacing: 0.5px;
    line-height: 1.1;
  }
  .person-role {
    font-size: 14px;
    font-weight: 400;
    margin-top: 2px;
  }

  .accent-band {
    position: absolute;
    top: 102px;
    height: 90px;
    background: var(--accent-orange);
  }
  .band-contact { left: 0; width: 300px; }
  .band-end { left: 382px; right: 0; }

  .contact-list {
    position: absolute;
    left: 104px;
    top: 116px;
    list-style: none;
  }
  .contact-item {
    display: flex;
    align-items: center;
    gap: 8px;
    font-size: 14px;
    line-height: 21px;
  }
  .contact-icon { width: 13px; height: 13px; flex: none; }

  .address {
    position: absolute;
    left: 196px;
    top: 226px;
    font-size: 15px;
    line-height: 22px;
    font-style: normal;
  }

  .brand {
    position: absolute;
    inset: 0;
    display: flex;
    align-items: center;
    justify-content: center;
  }
  .brand-name {
    font-size: 40px;
    font-weight: 500;
    letter-spacing: 0;
    color: var(--text-white);
  }
</style>
</head>
<body>
  <section class="business-card card-front">
    <div class="identity">
      <p class="person-name">DANIEL HARPER</p>
      <p class="person-role">Managing Director</p>
    </div>

    <div class="accent-band band-contact"></div>
    <div class="accent-band band-end"></div>

    <ul class="contact-list">
      <li class="contact-item">
        <svg class="contact-icon" viewBox="0 0 16 16" aria-hidden="true">
          <path fill="#fff" d="M3.6 1.5l2.2 2.6-1.3 1.6c.9 2 2.6 3.7 4.6 4.6l1.6-1.3 2.6 2.2-1.3 2.3C6.6 14.8 1.2 9.4 1.3 2.8z"/>
        </svg>
        <span>044-987 654 321</span>
      </li>
      <li class="contact-item">
        <svg class="contact-icon" viewBox="0 0 16 16" aria-hidden="true">
          <rect x="1" y="3" width="14" height="10" fill="#fff"/>
          <path d="M1 3l7 6 7-6" fill="none" stroke="#f7951f" stroke-width="1.4"/>
        </svg>
        <span>info@528builda.com</span>
      </li>
      <li class="contact-item">
        <svg class="contact-icon" viewBox="0 0 16 16" aria-hidden="true">
          <circle cx="8" cy="8" r="6.5" fill="none" stroke="#fff" stroke-width="1.4"/>
          <ellipse cx="8" cy="8" rx="2.8" ry="6.5" fill="none" stroke="#fff" stroke-width="1.2"/>
          <path d="M1.5 8h13M2.6 4.8h10.8M2.6 11.2h10.8" stroke="#fff" stroke-width="1"/>
        </svg>
        <span>www.528builda.com</span>
      </li>
    </ul>

    <address class="address">
      18 Linden Row, Suite 4<br>
      60612, Northvale
    </address>
  </section>

  <section class="business-card card-back">
    <div class="brand">
      <span class="brand-name">528BUILDA</span>
    </div>
  </section>
</body>
</html>
```